RW Framewell Inc Business cards

We need business cards using our existing logo but slightly modified. Right now the logo says RW Loadbearing Masonry. We want to keep the RW part of the design, but replace the Structural Concrete portion with "FRAMEWELL". Please see the attached file.
Ideally this would be a blank template so we can add Different Names, titles, and phone numbers later.
On the one side we want only the logo and on the other side the detail. I'm attaching an example for you to see.
Please reach out with any other questions. Our address and other details will be given out once we find a design we like.

Target Market(s)

Construction Industry

```html
<!DOCTYPE html>
<html lang="en">
<head>
<meta charset="utf-8">
<title>RW Framewell Inc – Business Cards</title>
<link href="https://fonts.googleapis.com/css2?family=Roboto:wght@400;500;700&display=swap" rel="stylesheet">
<style>
  :root {
    --backdrop: #eeeeee;
    --card-white: #fafafa;
    --brand-blue: #2274b0;
    --ink-grey: #5a5a5a;
    --rule-grey: #8a8a8a;
    --logo-white: #f2f2f2;
  }
  * { box-sizing: border-box; margin: 0; padding: 0; }
  html, body {
    width: 1200px; height: 987px; overflow: hidden;
    background: var(--backdrop);
    font-family: "Roboto", Arial, sans-serif;
  }
  .sheet {
    position: relative; width: 1200px; height: 987px;
    display: flex; align-items: center; justify-content: center; gap: 60px;
  }
  .card {
    position: relative; width: 520px; height: 297px;
    box-shadow: 0 2px 10px rgba(0,0,0,0.12);
  }
  /* Front: details side */
  .card--details { background: var(--card-white); }
  .accent-line {
    position: absolute; left: 0; top: 48px; width: 40px; height: 3px;
    background: var(--brand-blue);
  }
  .person { position: absolute; left: 56px; top: 36px; }
  .person__name {
    color: var(--brand-blue); font-weight: 700; font-size: 19px;
    letter-spacing: 0.5px; text-transform: uppercase;
  }
  .person__title { color: var(--ink-grey); font-weight: 700; font-size: 14px; margin-top: 2px; }
  .divider {
    position: absolute; left: 56px; right: 0; top: 152px; height: 1px;
    background: var(--rule-grey);
  }
  .contacts { position: absolute; left: 40px; top: 90px; list-style: none; }
  .contacts li {
    display: flex; align-items: center; gap: 8px;
    color: var(--ink-grey); font-size: 13.5px; line-height: 19px;
  }
  .contacts svg { width: 11px; height: 11px; fill: var(--brand-blue); flex: none; }
  .wordmark {
    position: absolute; right: 36px; top: 92px;
    display: flex; align-items: center; gap: 8px;
    color: var(--brand-blue); font-weight: 700; font-size: 22px; letter-spacing: 2px;
  }
  .wordmark__square { width: 14px; height: 14px; background: var(--brand-blue); }
  .address {
    position: absolute; right: 36px; top: 180px; text-align: right;
    color: var(--ink-grey); font-size: 15px; line-height: 21px;
  }
  /* Back: logo side */
  .card--logo {
    background: var(--brand-blue);
    display: flex; align-items: center; justify-content: center;
  }
  .card--logo .wordmark {
    position: static; color: var(--logo-white); font-size: 34px; letter-spacing: 4px; gap: 14px;
  }
  .card--logo .wordmark__square { width: 22px; height: 22px; background: var(--logo-white); }
</style>
</head>
<body>
<main class="sheet">
  <section class="card card--details" aria-label="Business card, details side">
    <span class="accent-line"></span>
    <div class="person">
      <p class="person__name">Martin Ellacott</p>
      <p class="person__title">Managing Director</p>
    </div>
    <ul class="contacts">
      <li><svg viewBox="0 0 12 12"><path d="M2 1h3l1 3-1.5 1a6 6 0 0 0 2.5 2.5L8 6l3 1v3a1 1 0 0 1-1 1A9 9 0 0 1 1 2a1 1 0 0 1 1-1z"/></svg>+1 905 555 0142</li>
      <li><svg viewBox="0 0 12 12"><path d="M1 3h10v7H1z M1 3l5 4 5-4" stroke="#fff" stroke-width="0.8"/></svg>martin@rwframewell.com</li>
      <li><svg viewBox="0 0 12 12"><circle cx="6" cy="6" r="5"/><path d="M1 6h10M6 1c-2.5 3-2.5 7 0 10M6 1c2.5 3 2.5 7 0 10" stroke="#fff" stroke-width="0.8" fill="none"/></svg>www.rwframewell.com</li>
    </ul>
    <div class="wordmark"><span class="wordmark__square"></span><span>RW FRAMEWELL</span></div>
    <span class="divider"></span>
    <p class="address">48 Quarry Ridge Road,<br>Brampton, ON L6P 3K1</p>
  </section>

  <section class="card card--logo" aria-label="Business card, logo side">
    <div class="wordmark"><span class="wordmark__square"></span><span>RW FRAMEWELL</span></div>
  </section>
</main>
</body>
</html>
```